Request for Business Card Design

Hi. My name is Marlene, I am looking for a new business card design for my company, Quarrow Signal Instruments, LLC. I really like the design you did for Tarsel Venture and was hoping you could do something similar using our full logo and our mark. I am also open to any raised texture design using our mark. I have attached our full logo, which would need to be somewhere on the card, as well as the mark in both outline and full form, as well as our brand colors / guide. The card does not have to be white, as long as our logo and mark appear. I actually like darker colored business cards more, but am open to all options. If you are interested in working with me, please let me know. We would also take the business card design into letterhead design if you can do that.

```html
<!DOCTYPE html>
<html lang="en">
<head>
<meta charset="utf-8">
<title>Quarrow Signal Instruments – Business Card</title>
<link rel="stylesheet" href="https://fonts.googleapis.com/css2?family=Barlow:wght@600&family=Open+Sans:wght@400;700&display=swap">
<style>
  :root {
    --backdrop: #3b3b3b;
    --card: #151515;
    --accent: #1a9bd0;
    --ink: #f2f2f2;
    --ink-soft: #d6d6d6;
    --relief-light: #9a9a9a;
    --relief-dark: #1c1c1c;
  }
  * { box-sizing: border-box; margin: 0; padding: 0; }
  html, body {
    width: 1200px; height: 801px; overflow: hidden;
    background: radial-gradient(ellipse at 50% 40%, #474747 0%, var(--backdrop) 70%);
  }
  .stage { position: relative; width: 1200px; height: 801px; }
  .card {
    position: absolute; top: 252px;
    width: 520px; height: 297px;
    background: var(--card);
    border-bottom: 3px solid var(--accent);
    border-left: 3px solid var(--accent);
    overflow: hidden;
    box-shadow: 0 18px 40px rgba(0,0,0,.45);
  }
  .card--back { left: 50px; }
  .card--front { left: 630px; }

  /* wordmark */
  .wordmark { font-family: "Barlow", sans-serif; font-weight: 600; color: var(--ink); line-height: 1; white-space: nowrap; }
  .wordmark__name { display: block; letter-spacing: 4px; }
  .wordmark__sub { display: block; letter-spacing: 1px; margin-top: 4px; }

  /* back side */
  .brand-lockup {
    position: absolute; left: 26px; top: 168px;
    display: flex; align-items: center; gap: 12px;
  }
  .brand-dot { width: 40px; height: 40px; border-radius: 50%; background: var(--accent); flex: none; }
  .brand-lockup .wordmark__name { font-size: 28px; letter-spacing: 3px; }
  .brand-lockup .wordmark__sub { font-size: 10px; }
  .divider {
    position: absolute; left: 280px; top: 62px; bottom: 0;
    width: 2px; background: var(--accent);
  }
  .divider::before {
    content: ""; position: absolute; left: 0; top: 0;
    width: 240px; height: 2px; background: var(--accent);
  }
  .contact {
    position: absolute; left: 300px; top: 80px;
    font-family: "Open Sans", sans-serif; color: var(--ink-soft);
    font-size: 12px; line-height: 1.45;
  }
  .contact__name { font-weight: 700; font-size: 16px; color: var(--accent); letter-spacing: .5px; }
  .contact__title { margin-bottom: 12px; }
  .contact__address { margin-bottom: 12px; }
  .contact__line { display: flex; align-items: center; gap: 8px; }
  .contact__line svg { width: 10px; height: 10px; fill: var(--accent); flex: none; }

  /* front side */
  .relief {
    position: absolute; right: -70px; top: -40px;
    width: 330px; height: 330px;
  }
  .front-mark { position: absolute; left: 38px; bottom: 26px; }
  .front-mark .wordmark__name { font-size: 44px; }
  .front-mark .wordmark__sub { font-size: 14px; }
</style>
</head>
<body>
<main class="stage">

  <section class="card card--back" aria-label="Card back with contact details">
    <div class="brand-lockup">
      <span class="brand-dot"></span>
      <span class="wordmark">
        <span class="wordmark__name">QUARROW</span>
        <span class="wordmark__sub">SIGNAL INSTRUMENTS</span>
      </span>
    </div>
    <div class="divider"></div>
    <div class="contact">
      <p class="contact__name">DORIAN VELCOURT</p>
      <p class="contact__title">President</p>
      <p class="contact__address">1180 Alder Crest Way<br>Harlow Bay CA 90417</p>
      <p class="contact__line">
        <svg viewBox="0 0 10 10"><path d="M2 0.5 3.6 2.8 2.6 3.9a6 6 0 0 0 3.5 3.5L7.2 6.4 9.5 8 8.6 9.5C4.5 9.5.5 5.5.5 1.4Z"/></svg>
        555-014-2287
      </p>
      <p class="contact__line">
        <svg viewBox="0 0 10 10"><path d="M0 2h10v6H0Zm1 .8L5 5.6 9 2.8Z"/></svg>
        d.velcourt@quarrow.com
      </p>
      <p class="contact__line">
        <svg viewBox="0 0 10 10"><circle cx="5" cy="5" r="5"/></svg>
        www.quarrow.com
      </p>
    </div>
  </section>

  <section class="card card--front" aria-label="Card front">
    <svg class="relief" viewBox="0 0 330 330" role="img" aria-label="Raised gloss brand emblem area">
      <defs>
        <radialGradient id="relief-fill" cx="70%" cy="40%" r="70%">
          <stop offset="0" stop-color="var(--relief-light)"/>
          <stop offset="1" stop-color="var(--relief-dark)"/>
        </radialGradient>
      </defs>
      <circle cx="165" cy="165" r="160" fill="url(#relief-fill)"/>
    </svg>
    <div class="front-mark wordmark">
      <span class="wordmark__name">QUARROW</span>
      <span class="wordmark__sub">SIGNAL INSTRUMENTS</span>
    </div>
  </section>

</main>
</body>
</html>
```